Website for designing and selling name-labels

We are looking for a fresh design for a site similar to these (www.tovskrabe.no, www.dremsgard.no, www.kvalbuffo.no) where the consumer can come online designing their own labels (30x15 mm) , either with onlye text or with text, choose a pre-defined symbol (which we have) and/or a color. We will the print the labels on our side, and send it to the customer.

We are looking for the front page, product page and check out - page.

Target Market(s)

families with childring, scools, kinder garden, industry

Number of Pages Required

3 page

Requirements
Nice to have
• bright and easy design
easy to design and see their own designs
easy check out - few steps

```html
<!DOCTYPE html>
<html lang="en">
<head>
<meta charset="utf-8">
<title>Lappeklar – Name tags</title>
<link rel="stylesheet" href="https://fonts.googleapis.com/css2?family=Poppins:wght@400;500;600;700;800&display=swap">
<style>
:root{
  --teal:#1a9e94;
  --teal-dark:#0b6e66;
  --sky:#a8dde9;
  --ink:#1c1c1c;
  --muted:#555;
  --footer:#363636;
  --white:#fff;
}
*{box-sizing:border-box;margin:0;padding:0}
html,body{width:1200px;height:3147px;overflow:hidden}
body{position:relative;font-family:"Poppins",sans-serif;color:var(--ink);background:var(--white)}
.abs{position:absolute}
/* header */
.logo{left:172px;top:20px;width:234px;height:63px;background:var(--teal);border-radius:8px;display:flex;align-items:center;justify-content:center;color:var(--white);font-weight:700;font-size:20px;letter-spacing:.5px}
.perks{right:172px;top:38px;display:flex;gap:14px;font-size:14px;color:#333;white-space:nowrap}
.perks span{display:flex;align-items:center;gap:6px}
.nav{left:0;top:106px;width:1200px;height:61px;background:var(--teal);border-bottom:2px solid var(--teal-dark)}
.nav ul{list-style:none;position:absolute;left:172px;width:856px;top:0;height:59px;display:flex;justify-content:space-between}
.nav li{color:var(--white);font-size:13.5px;display:flex;align-items:center;padding:0 10px;white-space:nowrap}
.nav li:last-child{padding-right:0}
.nav li.active{background:var(--teal-dark)}
/* hero */
.hero{left:0;top:167px;width:1200px;height:503px;background:linear-gradient(90deg,#bfe7ef 0%,var(--sky) 60%,#9fd6e4 100%)}
.hero-photo{left:0;top:0;width:520px;height:503px;background:linear-gradient(135deg,#b7e3ec 0%,#e9eef0 45%,#f1d25a 100%);opacity:.85}
.hero-title{left:589px;top:112px;font-size:62px;font-weight:800;color:var(--teal-dark);letter-spacing:1px;line-height:1}
.hero-sub{left:589px;top:200px;font-size:27px;color:var(--teal-dark);white-space:nowrap}
.btn{background:var(--teal-dark);color:var(--white);border-radius:40px;display:flex;align-items:center;justify-content:center;font-size:15px;white-space:nowrap}
.hero .btn{left:590px;top:278px;width:141px;height:61px;font-size:18px}
/* promo */
.sale{left:172px;top:739px;width:608px;height:306px;background:linear-gradient(135deg,#9ed8dc,#b5e1e0 50%,#f2c43a 52%,#ea6a3e 65%,#9ed8dc 68%)}
.tagpromo{left:794px;top:739px;width:234px;height:306px;background:linear-gradient(180deg,#6ea8dd,#4f8fd0)}
.tagpromo span{position:absolute;left:21px;bottom:14px;color:var(--white);font-size:19px;font-weight:500}
/* figures */
.h2{width:1200px;left:0;text-align:center;font-size:24px;font-weight:500}
.figs{left:172px;top:1182px;width:856px;display:flex;justify-content:space-between}
.fig{width:163px;height:149px;position:relative}
.fig span{position:absolute;top:6px;width:100%;text-align:center;color:var(--white);font-size:15px;font-weight:500}
/* category grid */
.cat{width:422px;height:340px}
.cat .card{position:absolute;left:39px;top:165px;width:346px;height:147px;background:rgba(255,255,255,.9);text-align:center}
.card h3{font-size:19px;font-weight:500;margin-top:20px}
.card p{font-size:12px;margin-top:6px}
.card .btn{margin:14px auto 0;width:108px;height:50px;font-size:14px}
/* testimonials */
.tcard{top:2296px;width:251px;height:307px;border:1px solid #555}
.tcard .q{position:absolute;left:22px;top:-22px;background:var(--white);padding:0 6px}
.tcard h4{position:absolute;left:22px;top:48px;font-size:16px;font-weight:500;white-space:nowrap}
.tcard p{position:absolute;left:22px;top:82px;width:203px;font-size:12px;line-height:27px;color:var(--muted);text-align:justify;letter-spacing:-.1px}
.tcard .who{position:absolute;left:22px;top:260px;color:var(--teal);font-size:15px}
.tcard .avatar{position:absolute;right:-13px;top:239px;width:86px;height:86px;border-radius:50%;border:3px solid var(--white);background:radial-gradient(circle,#c99a7a,#6a4a3a)}
/* footer */
.footer{left:0;top:2715px;width:1200px;height:432px;background:var(--footer);color:var(--white)}
.fcol{top:72px}
.fcol h5{font-size:18px;font-weight:500;margin-bottom:14px}
.fcol li{list-style:none;font-size:11.5px;line-height:27px;white-space:nowrap}
.rule{left:172px;top:339px;width:856px;height:1px;background:#777}
.copy{left:0;width:1200px;top:376px;text-align:center;font-size:12px}
</style>
</head>
<body>
<div class="abs logo">LAPPEKLAR.NO</div>
<div class="abs perks">
  <span><svg width="15" height="15" viewBox="0 0 24 24"><path fill="#1a9e94" d="M12 2l3 7 7 .6-5.3 4.7 1.7 7.2L12 17.8 5.6 21.5l1.7-7.2L2 9.6 9 9z"/></svg>Free shipping</span>
  <span><svg width="15" height="15" viewBox="0 0 24 24"><path fill="#1a9e94" d="M12 2l3 7 7 .6-5.3 4.7 1.7 7.2L12 17.8 5.6 21.5l1.7-7.2L2 9.6 9 9z"/></svg>Fast delivery</span>
  <span><svg width="15" height="15" viewBox="0 0 24 24"><path fill="#1a9e94" d="M12 2l3 7 7 .6-5.3 4.7 1.7 7.2L12 17.8 5.6 21.5l1.7-7.2L2 9.6 9 9z"/></svg>100% Satisfaction Gurantee</span>
</div>
<nav class="abs nav"><ul>
  <li class="active">Name tags</li><li>Name tags with familiar figures</li><li>Minilapper</li><li>Large name tags</li><li>Ironing pads</li><li>Door decorationNovelty</li>
</ul></nav>

<section class="abs hero">
  <div class="abs hero-photo" role="img" aria-label="Photo of baby bottles, soap, toy ducks and a sponge carrying name labels"></div>
  <h1 class="abs hero-title">LAPPEKLAR</h1>
  <p class="abs hero-sub">For a slightly easier everyday life</p>
  <a class="abs btn">SHOP NOW</a>
</section>

<div class="abs sale" role="img" aria-label="Sale banner with illustrated baby items around the word SALE"></div>
<div class="abs tagpromo" role="img" aria-label="Cloud shelf with hanging stars on blue"><span>NAME TAGS</span></div>

<h2 class="abs h2" style="top:1110px">Name tags with familiar figures</h2>
<div class="abs figs">
  <div class="fig" role="img" aria-label="Figure theme artwork" style="background:linear-gradient(180deg,#8fa0f5,#c7a5f0 70%,#7ad06a)"><span>Farm Friends</span></div>
  <div class="fig" role="img" aria-label="Figure theme artwork" style="background:linear-gradient(180deg,#2a4a8a,#6f8fc8)"><span>Winter Tales</span></div>
  <div class="fig" role="img" aria-label="Figure theme artwork" style="background:linear-gradient(180deg,#3a3a3a,#8a2b2b)"><span>City Climbers</span></div>
  <div class="fig" role="img" aria-label="Figure theme artwork" style="background:linear-gradient(180deg,#1e3a78,#b04a2a)"><span>Space Team</span></div>
  <div class="fig" role="img" aria-label="Figure theme artwork" style="background:radial-gradient(circle at 50% 45%,#f3d24a,#1a2a6a 65%)"><span>Cartoon Club</span></div>
</div>

<div class="abs cat" style="left:172px;top:1416px;background:linear-gradient(135deg,#d8d2ca,#b9a38a 60%,#3a3a3a)" role="img" aria-label="Cardboard boxes with large labels">
  <div class="card"><h3>Large Name Tags</h3><p>Large self-adhesive name tags for the equipment</p><a class="btn">SHOP NOW</a></div></div>
<div class="abs cat" style="left:605px;top:1416px;background:linear-gradient(135deg,#e9e1c8,#efe9de 55%,#c9a060 100%)" role="img" aria-label="Child's room with wall shelf and striped rug">
  <div class="card"><h3>Wall Decoration</h3><p>Create magical children's rooms</p><a class="btn">SHOP NOW</a></div></div>
<div class="abs cat" style="left:172px;top:1768px;background:linear-gradient(180deg,#dcaea3,#d4a294 70%,#eee)" role="img" aria-label="Teal backpack with baby clothes">
  <div class="card"><h3>Reflexes</h3><p>Be seen - use reflex</p><a class="btn">SHOP NOW</a></div></div>
<div class="abs cat" style="left:605px;top:1768px;background:linear-gradient(135deg,#d6d6d6,#ececec 50%,#8a8a8a)" role="img" aria-label="Hands placing an iron-on pad on a white shirt">
  <div class="card"><h3>Ironing pads</h3><p>For all types of clothing</p><a class="btn">SHOP NOW</a></div></div>

<h2 class="abs h2" style="top:2186px">Our Testimonials</h2>
<div class="abs tcard" style="left:172px">
  <svg class="q" width="64" height="40" viewBox="0 0 64 40"><path fill="#1a9e94" d="M10 0h18L16 40H0zM38 0h18L44 40H28z"/></svg>
  <h4>Very happy!</h4>
  <p>Very happy! Good quality and fast delivery. Very satisfied ! Fast and efficient. Good quality. Nemo enim ipsam voluptatem quia vo luptas sit aspernatur aut odit aut fugit, sed quias.</p>
  <span class="who">- Henrik S</span><div class="avatar" role="img" aria-label="Customer portrait"></div>
</div>
<div class="abs tcard" style="left:469px">
  <svg class="q" width="64" height="40" viewBox="0 0 64 40"><path fill="#1a9e94" d="M10 0h18L16 40H0zM38 0h18L44 40H28z"/></svg>
  <h4>Very satisfied</h4>
  <p>Very happy! Good quality and fast delivery. Very satisfied ! Fast and efficient. Good quality. Nemo enim ipsam voluptatem quia vo luptas sit aspernatur aut odit aut fugit, sed quias.</p>
  <span class="who">- Ingrid</span><div class="avatar" role="img" aria-label="Customer portrait"></div>
</div>
<div class="abs tcard" style="left:765px">
  <svg class="q" width="64" height="40" viewBox="0 0 64 40"><path fill="#1a9e94" d="M10 0h18L16 40H0zM38 0h18L44 40H28z"/></svg>
  <h4>Incredibly good service</h4>
  <p>Very happy! Good quality and fast delivery. Very satisfied ! Fast and efficient. Good quality. Nemo enim ipsam voluptatem quia vo luptas sit aspernatur aut odit aut fugit, sed quias.</p>
  <span class="who">- Sunniva</span><div class="avatar" role="img" aria-label="Customer portrait"></div>
</div>

<footer class="abs footer">
  <div class="abs fcol" style="left:171px"><h5>FOLLOW US</h5><ul>
    <li>Name tags</li><li>Name tags with familiar figures</li><li>Minilapper</li><li>Large name tags</li><li>Ironing pads</li><li>Door decoration</li><li>Other products</li></ul></div>
  <div class="abs fcol" style="left:478px"><h5>INSPIRATION</h5><ul>
    <li>Blog</li><li>Materials for kindergarten and school</li><li>Materials for old people's homes and</li><li>nursing homes</li><li>For business</li></ul></div>
  <div class="abs fcol" style="left:855px"><h5>CUSTOMER CENTER</h5><ul>
    <li>Contact Us</li><li>Questions and answers</li><li>Satisfaction guarantee</li></ul></div>
  <div class="abs rule"></div>
  <p class="abs copy">Copyrights @ 2021 Lappeklar. All Rights Reserved.</p>
</footer>
</body>
</html>
```